Commercial Rooftop Solar business needs a website

We need a website with fantastic appeal for a new company based in Melbourne called Tallow Ridge Energy. We design and install solar energy systems for commercial applications across Australia. Our market is to focus on small to medium businesses looking for solar solutions, but we will also provide our service for residential customers. We would like a beautiful 'front page' feel to our home page, using photographs of solar PV systems and/or natural imagery. Our logo uses the colours orange and black, which could easily be echoed in photographic imagery of sunset and sunrise, for example. The design should communicate quiet confidence and professionalism to a corporate marketplace.

NEW POINTS FOR BRIEF: This design also needs to be flexible to allow for additional future content, including a Support page with sub pages, FAQ's, and a Blog.

As part of this design project, we will require the coding for the website to be completed by the designer.

We have seen some websites, which we like the look and feel of: these are listed below.

brightvanepower.com.au:

• Beautiful images underlaying brief text selling points.
• Simple ‘front cover’ style home page with elegant drop-down menu, stylish simple font style.
• Home page invites exploration through the menu links, rather than trying to provide all the information up front.
• Company logo and name in the top left hand corner, contact details accessible at top right hand, seems consistent in most sites.

kelpworks.com.au

rumbofield.com:
• Same element as the others is the front-page style home page with beautiful images underlying text.

We have a webpage that we started uploading content to. You can use some of the content there in your designs: www.tallowridgeenergy.com.au

Technical Specifications:
PAGES:

Home

About Us

Solutions - Commercial
- Residential

Products - Solar Panels - Vorla Heron, Vorla TELD, Vorla QB
- Solar Inverters - Kestamo, BrilQuill
- Monitoring systems - Dunmere Metrics
- Batteries - RW

- Datasheets have been provided for reference but if it's too much work, you can use generic text and we will provide content later.

Contact Us

FUTURE PAGES (Please consider in structure, where links could be placed):

Support

FAQ's

Blog.

We could provide some content for the Support page soon, but the Blog and FAQ's are future pages which we don't want highlighted in the design as we don't yet have content.

Phone: 1800 7 BIRCH
Email: sales@tallowridgeenergy.com.au

Currently, I do not have images and text available. Please
use placeholders in the meantime. The final text and images will be uploaded for the winner once a winning design has been selected.

Target Market(s)

Primary focus is on small to medium sized business owners. Those owners will have a house which may be suitable for solar so we want to cater to residential deeper in the website.

Industry/Entity Type

Solar Energy

Coding

Coded - Design and coding required

Number of Pages Required

5+ page

Colors
f78f20
0255a3

Requirements
Must have
• Logo as per attachments.
Nice to have
• Logo can have alternate colours Eg. White on Orange or Black etc. provided colour correct logo is shown somewhere eg. footer or contact page.
• In the active site, I'd like to have:
• Very slowly zooming images - barely perceptible.
• Title text that rolls into place
• Subtle movements
• See https://plumtally.com.au/ for example

```html
<!DOCTYPE html>
<html lang="en">
<head>
<meta charset="utf-8">
<title>Tallow Ridge Energy</title>
<link href="https://fonts.googleapis.com/css2?family=Montserrat:wght@400;500;600;700&family=Open+Sans:wght@400;600&display=swap" rel="stylesheet">
<style>
:root{
  --orange:#f0592a;
  --orange-2:#f78f20;
  --black:#141414;
  --charcoal:#2b2b2b;
  --grey-bg:#ececec;
  --text:#444;
  --muted:#777;
  --white:#fff;
  --line:#cfcfcf;
}
*{box-sizing:border-box;margin:0;padding:0}
html,body{width:1200px;height:4110px;overflow:hidden}
body{font-family:"Open Sans",Arial,sans-serif;color:var(--text);background:var(--white);position:relative}
.h-font{font-family:"Montserrat",Arial,sans-serif}
a{color:inherit;text-decoration:none}

/* hero */
.hero{position:relative;height:603px;overflow:hidden}
.hero-photo{position:absolute;inset:0;background:linear-gradient(180deg,#7fa7d6 0%,#b8cfe6 38%,#3a4f78 52%,#2c3c63 62%,#5f8a2c 74%,#8fb340 100%)}
.site-header{position:absolute;top:0;left:0;right:0;height:130px;padding:0 70px 0 80px;display:flex;align-items:flex-start;justify-content:space-between}
.brand{display:flex;align-items:center;gap:10px;margin-top:40px;color:var(--white);font-family:"Montserrat",sans-serif;font-weight:600;font-size:24px}
.brand .dot{width:34px;height:34px;border-radius:50%;background:var(--white)}
.header-right{display:flex;flex-direction:column;align-items:flex-end;gap:20px;margin-top:20px}
.contact-row{display:flex;align-items:center;gap:22px}
.phone{display:flex;align-items:center;gap:8px;color:var(--white);font-family:"Montserrat",sans-serif;font-size:20px}
.btn-estimate{background:var(--orange);color:var(--white);font-family:"Montserrat",sans-serif;font-size:12px;font-weight:600;padding:9px 20px;border-radius:20px}
.main-nav{display:flex;gap:66px;color:var(--white);font-family:"Montserrat",sans-serif;font-size:15px;font-weight:600;margin-right:0}
.hero-title{position:absolute;left:0;right:0;top:495px;text-align:center;color:var(--white);font-family:"Montserrat",sans-serif;font-weight:600;font-size:32px;line-height:1.45;text-shadow:0 2px 6px rgba(0,0,0,.5)}
.slide-arrow{position:absolute;top:530px;color:var(--white);font-size:34px;opacity:.8}
.slide-arrow.prev{left:24px}.slide-arrow.next{right:24px}

/* services */
.services{display:flex;height:177px}
.service{flex:1;display:flex;align-items:center;gap:26px;padding:0 40px 0 80px;color:var(--white)}
.service.residential{background:var(--black)}
.service.commercial{background:var(--orange)}
.service-icon{width:106px;height:106px;border-radius:50%;flex:none;display:flex;align-items:center;justify-content:center}
.residential .service-icon{background:var(--orange)}
.commercial .service-icon{background:var(--white)}
.service h3{font-family:"Montserrat",sans-serif;font-size:22px;font-weight:600;margin-bottom:10px}
.commercial h3{color:var(--white)}
.service p{font-size:12.5px;line-height:1.55;max-width:370px}
.service p span{color:var(--orange)}
.commercial p span{color:var(--black)}

/* section titles */
.section-title{display:flex;align-items:center;justify-content:center;gap:24px;font-family:"Montserrat",sans-serif;font-weight:600;font-size:32px;color:var(--black);letter-spacing:.5px}
.section-title::before,.section-title::after{content:"";width:200px;height:1px;background:var(--line)}
.section-title em{font-style:normal;color:var(--orange)}
.btn{display:inline-block;background:var(--orange);color:var(--white);font-family:"Montserrat",sans-serif;font-weight:600;font-size:15px;padding:12px 26px;border-radius:24px}

/* about */
.about{height:492px;padding-top:42px;text-align:center}
.about p{font-size:14.5px;line-height:1.6;max-width:1030px;margin:0 auto;color:var(--text)}
.about .section-title{margin-bottom:36px}
.about p + p{margin-top:18px}
.about .btn{margin-top:30px}

/* products */
.products{background:var(--grey-bg);height:590px;padding-top:36px;position:relative}
.products .section-title{margin-bottom:40px}
.product-row{display:flex;justify-content:space-between;padding:0}
.product-card{width:386px;height:395px;background:#f4f4f4;border:1px solid #d4d4d4;position:relative}
.product-row .product-card:first-child{border-left:none;width:384px}
.product-row .product-card:last-child{border-right:none;width:384px}
.panel-img{position:absolute;left:50%;top:48px;transform:translateX(-50%);width:160px;height:240px;border:3px solid #c9ccd2}
.panel-img.blue{background:linear-gradient(160deg,#3e4f9a,#1f2b6b)}
.panel-img.black{background:linear-gradient(160deg,#2a2a2a,#0b0b0b)}
.product-label{position:absolute;left:0;top:270px;width:335px;height:76px;padding:14px 20px;border-radius:0 38px 38px 0;font-family:"Montserrat",sans-serif;font-weight:600;font-size:19px;line-height:1.25;color:var(--white);background:var(--black);box-shadow:0 3px 6px rgba(0,0,0,.3)}
.product-label.hot{background:var(--orange)}
.view-all{position:absolute;left:0;right:0;bottom:28px;text-align:center;font-family:"Montserrat",sans-serif;font-weight:600;font-size:15px;color:var(--orange);text-decoration:underline}

/* why choose */
.why{height:670px;position:relative;background:linear-gradient(120deg,#f7f7f7 0%,#eceff3 55%,#dfe5ec 100%);padding-top:58px}
.why-diagram{position:absolute;left:0;top:130px;width:1200px;height:520px}
.feature{position:absolute;display:flex;align-items:center;gap:18px;font-size:15px;line-height:1.4;color:var(--black)}
.feature.left{flex-direction:row-reverse;text-align:right;width:330px}
.feature .ficon{width:62px;height:62px;border-radius:50%;background:var(--orange);box-shadow:0 0 0 5px rgba(240,89,42,.25);flex:none;display:flex;align-items:center;justify-content:center}
.why-centre{position:absolute;left:512px;top:165px;width:180px;text-align:center;font-family:"Montserrat",sans-serif;font-weight:700;font-size:22px;color:var(--orange);line-height:1.2}

/* promise banner */
.promise{height:400px;position:relative}
.promise-photo{position:absolute;inset:0;background:linear-gradient(90deg,#d58a3a 0%,#f0b45a 30%,#f3c770 50%,#c3a34c 70%,#9a8a3d 100%)}
.promise-box{position:absolute;right:0;top:130px;width:650px;height:170px;background:linear-gradient(90deg,rgba(240,89,42,0) 0%,rgba(240,89,42,.92) 18%,var(--orange) 100%);border-radius:50px 0 0 50px;color:var(--white);font-family:"Montserrat",sans-serif;font-weight:600;font-size:25px;line-height:1.35;text-align:center;padding:30px 30px 0 120px}

/* stats */
.stats{height:300px;background:linear-gradient(180deg,#3c4a5e,#1f2836);display:flex;justify-content:center;gap:22px;padding-top:55px}
.stat{width:247px;height:192px;background:var(--black);color:var(--white);text-align:center;padding-top:22px}
.stat .num{font-family:"Montserrat",sans-serif;font-weight:600;font-size:34px;margin:14px 0 8px}
.stat p{font-size:11.5px;line-height:1.5;padding:0 20px;color:#ddd}

/* quote form */
.savings{height:597px;position:relative;padding-top:52px;text-align:center}
.savings .section-title em{color:var(--orange)}
.savings-intro{font-size:15px;margin-top:34px}
.house-art{position:absolute;left:0;bottom:0;width:420px;height:360px;background:linear-gradient(180deg,#eef2f5,#c9d3db)}
.city-art{position:absolute;right:0;bottom:0;width:190px;height:200px;background:linear-gradient(180deg,#f4f6f8,#dde3e8)}
.quote-form{position:absolute;left:430px;top:205px;width:627px;display:grid;grid-template-columns:1fr 1fr;gap:11px 17px;text-align:left}
.field{height:32px;border:1px solid #d6d6d6;background:var(--white);font-size:11px;color:#888;padding:8px 10px;position:relative}
.field.select::after{content:"";position:absolute;right:10px;top:12px;border:5px solid transparent;border-top-color:#555}
.field.wide{grid-column:1 / 3;height:70px}
.quote-form .btn{justify-self:start;font-size:15px;padding:11px 30px;margin-top:8px}

/* referral */
.referral{height:68px;background:var(--black);color:var(--white);display:flex;align-items:center;justify-content:center;gap:40px;font-family:"Montserrat",sans-serif;font-size:24px}
.referral .btn{font-size:14px;padding:8px 28px}

/* footer */
.site-footer{height:340px;background:var(--charcoal);color:var(--white);display:grid;grid-template-columns:240px 290px 300px 1fr;padding:45px 0 0 80px}
.site-footer h4{font-family:"Montserrat",sans-serif;font-weight:600;font-size:17px;margin-bottom:28px}
.quick-links li{list-style:none;font-size:13.5px;margin-bottom:22px}
.quick-links li::before{content:"›";margin-right:14px}
.contact-item{display:flex;gap:12px;font-size:13.5px;line-height:1.45;margin-bottom:18px}
.c-ic{width:26px;height:26px;border-radius:50%;background:var(--orange);flex:none;display:flex;align-items:center;justify-content:center}
.map{width:220px;height:120px;background:linear-gradient(135deg,#e9ece6,#d5dccd)}
.socials{display:flex;gap:14px}
.socials span{width:38px;height:38px;border-radius:50%;background:var(--orange)}
.footer-brand{margin-top:48px;font-family:"Montserrat",sans-serif;font-weight:600;font-size:22px;color:var(--orange);display:flex;align-items:center;gap:10px}
.footer-brand i{width:24px;height:24px;border-radius:50%;background:var(--orange);display:block}
.legal{height:50px;background:var(--orange);color:var(--white);font-size:13px;display:flex;align-items:center;justify-content:center}
</style>
</head>
<body>

<section class="hero">
  <div class="hero-photo" role="img" aria-label="Ground-mounted solar panel arrays on green grass under a blue sky"></div>
  <header class="site-header">
    <a class="brand" href="#"><span class="dot"></span>Tallow Ridge Energy</a>
    <div class="header-right">
      <div class="contact-row">
        <span class="phone">
          <svg width="26" height="26" viewBox="0 0 26 26"><circle cx="13" cy="13" r="12" fill="none" stroke="#fff" stroke-width="1.6"/><path d="M9 7l3 3-1.5 2c.8 1.6 2 2.8 3.5 3.5l2-1.5 3 3-2 2c-5 0-10-5-10-10z" fill="#fff"/></svg>
          (123) 456-7890</span>
        <a class="btn-estimate" href="#">FREE ESTIMATE</a>
      </div>
      <nav class="main-nav"><a href="#">HOME</a><a href="#">ABOUT US</a><a href="#">SOLUTIONS</a><a href="#">CONTACT US</a></nav>
    </div>
  </header>
  <span class="slide-arrow prev">‹</span><span class="slide-arrow next">›</span>
  <h1 class="hero-title">Tallow Ridge Energy Is A National Company That Specialises<br>In Solar Solutions For The Commercial Market</h1>
</section>

<section class="services">
  <div class="service residential">
    <div class="service-icon"><svg width="54" height="50" viewBox="0 0 54 50"><path d="M27 3L3 24h7v23h34V24h7z" fill="#fff"/><rect x="22" y="30" width="10" height="17" fill="#f0592a"/><rect x="13" y="28" width="6" height="6" fill="#f0592a"/><rect x="35" y="28" width="6" height="6" fill="#f0592a"/></svg></div>
    <div><h3>RESIDENTIAL SERVICES</h3><p>Clean rooftop solar for family homes, designed and installed by our own team with care, quality parts and support that lasts well beyond handover day...<span>[+]</span></p></div>
  </div>
  <div class="service commercial">
    <div class="service-icon"><svg width="50" height="54" viewBox="0 0 50 54"><rect x="8" y="4" width="34" height="48" fill="#141414"/><g fill="#fff"><rect x="13" y="10" width="6" height="6"/><rect x="22" y="10" width="6" height="6"/><rect x="31" y="10" width="6" height="6"/><rect x="13" y="20" width="6" height="6"/><rect x="22" y="20" width="6" height="6"/><rect x="31" y="20" width="6" height="6"/><rect x="13" y="30" width="6" height="6"/><rect x="22" y="30" width="6" height="6"/><rect x="31" y="30" width="6" height="6"/><rect x="21" y="41" width="8" height="11"/></g></svg></div>
    <div><h3>COMMERCIAL SERVICES</h3><p>Scalable solar systems for small and medium businesses that cut running costs, with clear reporting and a team that stays on call...<span>[+]</span></p></div>
  </div>
</section>

<section class="about">
  <h2 class="section-title">ABOUT&nbsp;<em>TALLOW RIDGE ENERGY</em></h2>
  <p>Tallow Ridge Energy is a national company that specialises in solar solutions for the commercial market. We also provide solutions for the residential market, bringing our uncompromising quality and service to the home.</p>
  <p>The founder of the company has over 10 years experience delivering projects on both a residential and commercial scale, having overseen the installation of more than 3 megawatts of solar projects. They were a pioneer on the first megawatt scale project in Australia.</p>
  <a class="btn" href="#">READ MORE</a>
</section>

<section class="products">
  <h2 class="section-title">OUR&nbsp;<em>PRODUCTS</em></h2>
  <div class="product-row">
    <article class="product-card"><div class="panel-img blue" role="img" aria-label="Blue polycrystalline solar panel"></div><div class="product-label">Vorla Heron<br>- The Budget Workhorse</div></article>
    <article class="product-card"><div class="panel-img blue" role="img" aria-label="Blue solar panel with product box"></div><div class="product-label hot">Vorla Heron QB<br>- Optimised and Flexible</div></article>
    <article class="product-card"><div class="panel-img black" role="img" aria-label="Black monocrystalline solar panel"></div><div class="product-label">Vorla Heron TELD<br>- Beautiful Power</div></article>
  </div>
  <a class="view-all" href="#">VIEW ALL &nbsp;»</a>
</section>

<section class="why">
  <h2 class="section-title">WHY CHOOSE&nbsp;<em>TALLOW RIDGE ENERGY</em></h2>
  <div class="why-diagram">
    <svg width="1200" height="520" style="position:absolute;left:0;top:0">
      <circle cx="600" cy="210" r="200" fill="none" stroke="#555" stroke-width="1"/>
      <g stroke="#444" stroke-width="1" fill="none">
        <path d="M420 140 L490 80 H555"/><path d="M780 140 L710 80 H645"/>
        <path d="M400 210 H480"/><path d="M800 210 H720"/>
        <path d="M420 280 L490 340 H555"/><path d="M780 280 L710 340 H645"/>
      </g>
      <g fill="#1e3a5f"><circle cx="482" cy="65" r="4"/><circle cx="718" cy="65" r="4"/><circle cx="400" cy="210" r="4"/><circle cx="800" cy="210" r="4"/><circle cx="482" cy="355" r="4"/><circle cx="718" cy="355" r="4"/></g>
    </svg>
    <div class="why-centre">TALLOW<br>RIDGE<br>ENERGY</div>
    <div class="feature left" style="left:85px;top:50px"><span class="ficon"><svg width="26" height="30" viewBox="0 0 26 30"><path d="M13 1a10 10 0 0 0-10 10c0 8 10 18 10 18s10-10 10-18A10 10 0 0 0 13 1z" fill="#fff"/><circle cx="13" cy="11" r="4" fill="#f0592a"/></svg></span>100% Locally<br>Owned &amp; Operated</div>
    <div class="feature left" style="left:85px;top:218px"><span class="ficon"><svg width="30" height="30" viewBox="0 0 30 30"><circle cx="15" cy="15" r="11" fill="none" stroke="#fff" stroke-width="3"/><circle cx="15" cy="15" r="5" fill="#fff"/></svg></span>Top Quality<br>Components</div>
    <div class="feature left" style="left:85px;top:386px"><span class="ficon"><svg width="30" height="28" viewBox="0 0 30 28"><circle cx="15" cy="8" r="6" fill="#fff"/><path d="M3 27c0-7 5-11 12-11s12 4 12 11z" fill="#fff"/></svg></span>Ranked Top Solar<br>Contractor Nationally</div>
    <div class="feature" style="left:785px;top:50px"><span class="ficon"><svg width="28" height="30" viewBox="0 0 28 30"><circle cx="14" cy="11" r="9" fill="#fff"/><path d="M8 18l-3 11 9-5 9 5-3-11z" fill="#fff"/></svg></span>Top Quality Components</div>
    <div class="feature" style="left:785px;top:218px"><span class="ficon"><svg width="30" height="30" viewBox="0 0 30 30"><circle cx="15" cy="15" r="6" fill="#fff"/><g stroke="#fff" stroke-width="2.5"><path d="M15 2v5M15 23v5M2 15h5M23 15h5M6 6l3 3M21 21l3 3M24 6l-3 3M9 21l-3 3"/></g></svg></span>Over 3,000 Installations<br>In New England</div>
    <div class="feature" style="left:785px;top:386px"><span class="ficon"><svg width="28" height="28" viewBox="0 0 28 28"><path d="M5 15l6 6 12-14" fill="none" stroke="#fff" stroke-width="4"/></svg></span>Vertically Integrated</div>
  </div>
</section>

<section class="promise">
  <div class="promise-photo" role="img" aria-label="Mother and child embracing in a sunlit field at golden hour"></div>
  <div class="promise-box">We Go the Extra Mile to Support Our Customers and They Have Made Us the #1 Residential Solar Installer in the State.</div>
</section>

<section class="stats">
  <div class="stat"><svg width="38" height="38" viewBox="0 0 38 38" fill="none" stroke="#fff" stroke-width="2"><path d="M8 4v30M19 4v30M30 4v30"/><rect x="4" y="10" width="8" height="5" fill="#141414"/><rect x="15" y="22" width="8" height="5" fill="#141414"/><rect x="26" y="14" width="8" height="5" fill="#141414"/></svg><div class="num">72%</div><p>Amount Electricity prices rose in five years until June 2012</p></div>
  <div class="stat"><svg width="38" height="38" viewBox="0 0 38 38" fill="none" stroke="#fff" stroke-width="2"><rect x="7" y="3" width="24" height="32" rx="2"/><rect x="11" y="7" width="16" height="7"/><path d="M12 20h3M18 20h3M24 20h3M12 26h3M18 26h3M24 26h3"/></svg><div class="num">29%</div><p>The predicted amount electricity prices will rise by 2020</p></div>
  <div class="stat"><svg width="44" height="38" viewBox="0 0 44 38" fill="none" stroke="#fff" stroke-width="2"><rect x="3" y="8" width="38" height="22"/><text x="22" y="25" fill="#fff" stroke="none" font-size="14" text-anchor="middle" font-family="Arial">$</text></svg><div class="num">$19Billion</div><p>has been invested into renewable energy in Australia since 2001</p></div>
  <div class="stat"><svg width="38" height="38" viewBox="0 0 38 38" fill="none" stroke="#fff" stroke-width="2"><path d="M19 3a11 11 0 0 0-6 20v5h12v-5a11 11 0 0 0-6-20zM14 32h10M16 36h6"/></svg><div class="num">2320MW</div><p>RECORDED SOLAR Photovoltaic INSTALLED IN AUSTRALIA in 2012</p></div>
</section>

<section class="savings">
  <h2 class="section-title">YOUR SOLAR&nbsp;<em>SAVINGS START HERE!</em></h2>
  <p class="savings-intro">We want to help you reduce or eliminate your utility bill and make Massachusetts a cleaner place to live, work, and enjoy life.</p>
  <div class="house-art" role="img" aria-label="Illustration of a modern house with rooftop solar panels and a wind turbine"></div>
  <div class="city-art" role="img" aria-label="Faint illustration of an industrial skyline"></div>
  <form class="quote-form">
    <div class="field">First Name *</div><div class="field">LastName *</div>
    <div class="field">Email *</div><div class="field">Phone *</div>
    <div class="field">Address *</div><div class="field select">City *</div>
    <div class="field select">State *</div><div class="field select">Zip Code *</div>
    <div class="field select">Solar for home or business?</div><div class="field select">Where are you in your solar purchasing journey?</div>
    <div class="field wide">Comments</div>
    <a class="btn" href="#">GET MY FREE QUOTE</a>
  </form>
</section>

<section class="referral">
  <span>Help a Friend Go Solar. Ask About Our Referral Program.</span>
  <svg width="50" height="16" viewBox="0 0 50 16"><path d="M1 6c14 6 30 6 44 2" fill="none" stroke="#fff" stroke-width="1.5"/><path d="M40 3l7 5-8 3" fill="none" stroke="#fff" stroke-width="1.5"/></svg>
  <a class="btn" href="#">MORE INFORMATION</a>
</section>

<footer class="site-footer">
  <div><h4>QUICK LINKS</h4><ul class="quick-links"><li>Home</li><li>About Us</li><li>Solutions</li><li>Contact Us</li></ul></div>
  <div><h4>CONTACT DETAILS</h4>
    <div class="contact-item"><span class="c-ic"><svg width="12" height="14" viewBox="0 0 12 14"><path d="M6 0a5 5 0 0 0-5 5c0 4 5 9 5 9s5-5 5-9a5 5 0 0 0-5-5z" fill="#fff"/></svg></span><span><b>TALLOW RIDGE ENERGY</b><br>123 Harbour Lane, Suite 4,<br>Melbourne VIC</span></div>
    <div class="contact-item"><span class="c-ic"><svg width="12" height="12" viewBox="0 0 12 12"><path d="M2 1l2.5 2.5-1 1.5c.7 1.4 1.6 2.3 3 3l1.5-1L10.5 9.5 9 11C5 11 1 7 1 3z" fill="#fff"/></svg></span><span>(123) 456-7890</span></div>
    <div class="contact-item"><span class="c-ic"><svg width="13" height="10" viewBox="0 0 13 10"><rect x="0.5" y="0.5" width="12" height="9" fill="none" stroke="#fff"/><path d="M1 1l5.5 5L12 1" fill="none" stroke="#fff"/></svg></span><span>info@tallowridgeenergy.com.au</span></div>
  </div>
  <div><h4>LOCATION MAP</h4><div class="map" role="img" aria-label="Street map showing the office location"></div></div>
  <div><h4>FOLLOW US</h4><div class="socials"><span aria-label="Social link"></span><span aria-label="Social link"></span><span aria-label="Social link"></span><span aria-label="Social link"></span></div>
    <div class="footer-brand"><i></i>Tallow Ridge Energy</div></div>
</footer>
<div class="legal">© 2017 TALLOW RIDGE ENERGY . All rights reserved &nbsp;|&nbsp; Privacy Policy</div>

</body>
</html>
```